MRT Property - Business Cards

Looking for a business card & general letterhead, signage etc design for our new logo.

Colours:
000a20
0056a2
00b5ef
0088ce
68cef2

Fonts:
Poppins
Karla

Please keep look and feel of new brand - example in the zip package I sent.

```html
<!DOCTYPE html>
<html lang="en">
<head>
<meta charset="utf-8">
<title>MRT Property – Business Cards</title>
<link href="https://fonts.googleapis.com/css2?family=Poppins:wght@400;500;600;700&display=swap" rel="stylesheet">
<style>
  :root {
    --navy: #000a20;
    --royal: #0056a2;
    --cyan: #00b5ef;
    --azure: #0088ce;
    --sky: #68cef2;
    --white: #ffffff;
    --stage: #3d3d3d;
  }
  * { margin: 0; padding: 0; box-sizing: border-box; }
  html, body { width: 1200px; height: 803px; overflow: hidden; }
  body {
    background: var(--stage);
    font-family: "Poppins", sans-serif;
    position: relative;
  }
  .card {
    position: absolute;
    top: 258px;
    width: 500px;
    height: 286px;
    border-radius: 22px;
    overflow: hidden;
  }
  .card--front { left: 60px; background: var(--white); }
  .card--back { left: 640px; background: var(--azure); }

  .front-band { position: absolute; inset: 0; width: 100%; height: 100%; }

  .wordmark {
    position: absolute;
    display: flex;
    align-items: center;
    gap: 8px;
    font-weight: 600;
    white-space: nowrap;
  }
  .wordmark__dot { border-radius: 50%; flex: none; }
  .wordmark--front { right: 22px; top: 124px; color: var(--royal); font-size: 17px; }
  .wordmark--front .wordmark__dot { width: 14px; height: 14px; background: var(--sky); }
  .wordmark--back {
    left: 0; right: 0; top: 0; bottom: 0;
    justify-content: center;
    color: var(--cyan);
    font-size: 46px;
    gap: 16px;
  }
  .wordmark--back .wordmark__dot { width: 34px; height: 34px; background: var(--royal); }

  .contact {
    position: absolute;
    left: 36px;
    top: 40px;
    color: var(--white);
  }
  .contact__name { font-size: 22px; font-weight: 700; line-height: 1.1; }
  .contact__role { font-size: 11px; font-weight: 400; margin-bottom: 26px; }
  .contact__address { font-size: 11px; line-height: 1.35; margin-bottom: 10px; }
  .contact__list { list-style: none; font-size: 11px; line-height: 1.45; }
  .contact__list li { display: flex; align-items: center; gap: 8px; }
  .contact__icon { width: 10px; height: 10px; flex: none; }
</style>
</head>
<body>

<section class="card card--front" aria-label="Business card front">
  <svg class="front-band" viewBox="0 0 500 286" preserveAspectRatio="none" aria-hidden="true">
    <path d="M0 0 H292 Q352 143 306 286 H0 Z" fill="var(--royal)"/>
    <path d="M300 0 Q362 143 318 286" fill="none" stroke="var(--royal)" stroke-width="3"/>
  </svg>

  <div class="wordmark wordmark--front">
    <span class="wordmark__dot"></span>
    <span class="wordmark__name">MRT Property</span>
  </div>

  <div class="contact">
    <p class="contact__name">Daniel Reeve</p>
    <p class="contact__role">President</p>
    <p class="contact__address">4102 Willow Crest Road<br>Halden, Canada 58213</p>
    <ul class="contact__list">
      <li>
        <svg class="contact__icon" viewBox="0 0 10 10" aria-hidden="true"><path d="M2 1 L4 1 L4.6 3 L3.5 4 Q4.5 6 6 6.6 L7 5.5 L9 6 L9 8 Q5 9 2.2 6.5 Q0.8 4 2 1Z" fill="var(--white)"/></svg>
        555-210-4832
      </li>
      <li>
        <svg class="contact__icon" viewBox="0 0 10 10" aria-hidden="true"><rect x="2.5" y="0.5" width="5" height="9" rx="1" fill="none" stroke="var(--white)"/></svg>
        555-310-7719
      </li>
      <li>
        <svg class="contact__icon" viewBox="0 0 10 10" aria-hidden="true"><rect x="0.5" y="2" width="9" height="6.5" fill="none" stroke="var(--white)"/><path d="M0.5 2 L5 6 L9.5 2" fill="none" stroke="var(--white)"/></svg>
        info@mrtproperty.com
      </li>
      <li>
        <svg class="contact__icon" viewBox="0 0 10 10" aria-hidden="true"><circle cx="5" cy="5" r="4.5" fill="var(--white)"/></svg>
        www.mrtproperty.com
      </li>
    </ul>
  </div>
</section>

<section class="card card--back" aria-label="Business card back">
  <div class="wordmark wordmark--back">
    <span class="wordmark__dot"></span>
    <span class="wordmark__name">MRT Property</span>
  </div>
</section>

</body>
</html>
```